Non Profit Company Looking For New Website

The website for Fernvale Quillstone Heritage Society should offer the viewer beautiful photos that inspire condifence and joy and tap into our love of horses.

We would like to see a website that displays trust, quality and confidence. Needs to be responsive and mobile friendly for all browsers and coded for both Android & IOS.

READ ATTACHED WEBSITE TEMPLATE FOR COMPLETE DETAILS ON WHAT WE ARE LOOKING FOR.

Looking for recommmendations if we should use WordPress/WooCommerce for site or Wordpress with Shopify Plug in or just Shopify.

Must be both desktop and mobile friendly with fast page load speed. Need the ability to edit ourselves.

Industry/Entity Type

Non Profit

Coding

Coded - Design and coding required

Number of Pages Required

5+ page

Requirements
Must have
• We would like to see a website that displays trust, quality and confidence. Needs to be responsive and mobile friendly for all browsers and coded for both Android & IOS.

Looking for recommendations if we should use WordPress/WooCommerce for site or Wordpress with Shopify Plug in or just Shopify.

Logo Colour:
Pantone 7621 C

READ TEMPLATE THAT IS ATTACHED
Nice to have
• Like look of this website as a sample:
https://www.quellbrimtorva.com/

Another similar non profit organization
https://pellaworthcindle.com/

```html
<!DOCTYPE html>
<html lang="en">
<head>
<meta charset="utf-8">
<title>Fernvale Quillstone Heritage Society</title>
<link rel="stylesheet" href="https://fonts.googleapis.com/css2?family=Cinzel:wght@500;600&family=Montserrat:wght@400;500;600;700&family=Playfair+Display:ital@1&display=swap">
<style>
:root{
  --red:#a51f2b;
  --red-dark:#8e1822;
  --ink:#2b2b2b;
  --text:#444;
  --grey-line:#a9a9a9;
  --panel-grey:#626262;
  --footer:#2b2b2b;
  --white:#fff;
}
*{box-sizing:border-box;margin:0;padding:0}
html,body{width:1200px;height:4024px;overflow:hidden}
body{position:relative;background:var(--white);font-family:"Montserrat",sans-serif;color:var(--text)}
.abs{position:absolute}
.serif{font-family:"Cinzel",serif;font-weight:500}

/* header */
.site-header{position:absolute;left:0;top:0;width:1200px;height:86px;background:var(--white);z-index:3}
.brand{position:absolute;left:94px;top:18px;width:240px;display:flex;align-items:center;gap:10px}
.brand-dot{width:14px;height:14px;border-radius:50%;background:var(--red);flex:none}
.brand-name{font-family:"Cinzel",serif;font-weight:600;font-size:15px;line-height:18px;color:var(--red)}
.main-nav a{position:absolute;top:36px;font-size:12px;font-weight:600;color:#333;text-decoration:none;letter-spacing:.3px;transform:translateX(-50%)}
.main-nav a.active{color:var(--red)}
.main-nav a.active::after{content:"";position:absolute;left:0;right:0;bottom:-8px;height:2px;background:var(--red)}
.phone-btn{position:absolute;left:948px;top:24px;width:169px;height:40px;border-radius:20px;background:var(--red);color:var(--white);font-size:14px;font-weight:600;display:flex;align-items:center;justify-content:center;gap:8px}

/* hero */
.hero{position:absolute;left:0;top:86px;width:1200px;height:640px}
.hero-badge{position:absolute;left:102px;top:172px;width:406px;height:406px;border-radius:50%;border:4px solid rgba(255,255,255,.85);display:flex;align-items:center;justify-content:center}
.hero-badge-inner{width:368px;height:368px;border-radius:50%;background:rgba(165,31,43,.88);color:var(--white);text-align:center;display:flex;flex-direction:column;justify-content:center}
.hero-badge .lead{font-size:20px;line-height:28px;font-weight:500}
.hero-badge .big{font-size:29px;line-height:36px;font-weight:700;margin-top:8px}
.hero-arrow{position:absolute;top:352px}

/* timeline */
.tl{position:absolute;left:0;top:0;width:1200px;height:4024px;pointer-events:none;z-index:1}

/* copy blocks */
.sect-title{position:absolute;color:var(--red);font-family:"Cinzel",serif;font-weight:500;text-align:center}
.btn-outline{position:absolute;border:2px solid var(--red);border-radius:24px;color:var(--red);font-size:14px;font-weight:700;display:flex;align-items:center;justify-content:center;background:var(--white)}
.copy{position:absolute;text-align:center}

/* adopt circle */
.adopt-ring{position:absolute;left:609px;top:1897px;width:456px;height:456px;border-radius:50%;border:2px solid var(--red);display:flex;align-items:center;justify-content:center}
.adopt-disc{width:428px;height:428px;border-radius:50%;background:var(--red);color:var(--white);text-align:center;position:relative}

/* horses */
.section-heading{position:absolute;left:0;width:1200px;text-align:center;font-family:"Cinzel",serif;font-weight:500;font-size:37px;color:var(--ink)}
.horse-card{position:absolute;width:332px;height:235px}
.horse-card svg{display:block}
.horse-info{position:absolute;left:0;bottom:0;width:100%;padding:0 18px 10px;color:var(--white)}
.horse-info .name{font-family:"Playfair Display",serif;font-style:italic;font-size:24px;padding-bottom:10px;border-bottom:1px solid rgba(255,255,255,.5)}
.horse-info .facts{display:grid;grid-template-columns:1fr 1fr;font-size:12px;line-height:22px;margin-top:6px}
.horse-info b{font-weight:700}
.btn-solid{position:absolute;background:var(--red);color:var(--white);border-radius:29px;font-size:15px;font-weight:700;display:flex;align-items:center;justify-content:center}

/* contact */
.footer-band{position:absolute;left:0;top:3567px;width:1200px;height:457px;background:linear-gradient(180deg,#3a3a3a,#1f1f1f)}
.contact-card{position:absolute;left:112px;top:3336px;width:974px;height:398px;border-radius:16px;overflow:hidden;background:var(--panel-grey);z-index:2}
.contact-item{position:absolute;left:66px;color:var(--white)}
.contact-item .icon{position:absolute;left:0;width:56px;height:56px;border-radius:50%;background:var(--white);display:flex;align-items:center;justify-content:center}
.contact-item .label{position:absolute;left:144px;font-size:13px;font-weight:700;white-space:nowrap}
.contact-item .val{position:absolute;left:144px;font-size:11px;line-height:25px;white-space:nowrap}
.field{position:absolute;border-bottom:2px solid #cfcfcf;color:#eee;font-size:12px;font-weight:600;display:flex;align-items:center;gap:7px;padding-bottom:12px}
.check-box{position:absolute;left:455px;top:305px;width:221px;height:54px;background:#f7f7f7;border:1px solid #d3d3d3;border-radius:3px;display:flex;align-items:center;gap:10px;padding-left:12px;font-size:10px;color:#333}
.check-box span.box{width:20px;height:20px;border:2px solid #c1c1c1;border-radius:2px;background:var(--white)}
.send-btn{position:absolute;left:733px;top:305px;width:166px;height:42px;border-radius:21px;background:var(--white);color:var(--red);font-size:14px;font-weight:700;display:flex;align-items:center;justify-content:center}

/* footer */
.footer-brand{position:absolute;left:0;top:3782px;width:1200px;text-align:center;font-family:"Cinzel",serif;font-weight:600;font-size:18px;color:var(--white)}
.footer-nav a{position:absolute;top:3854px;transform:translateX(-50%);color:var(--white);font-size:13px;font-weight:700;text-decoration:none}
.copyright{position:absolute;left:0;top:3892px;width:1200px;text-align:center;color:#ccc;font-size:11px}
</style>
</head>
<body>

<header class="site-header">
  <div class="brand"><span class="brand-dot"></span><span class="brand-name">Fernvale Quillstone<br>Heritage Society</span></div>
  <nav class="main-nav">
    <a class="active" style="left:366px">HOME</a>
    <a style="left:458px">ABOUT</a>
    <a style="left:553px">ADOPT</a>
    <a style="left:653px">HORSES</a>
    <a style="left:756px">DONATE</a>
    <a style="left:867px">CONTACT</a>
  </nav>
  <div class="phone-btn">
    <svg width="18" height="18" viewBox="0 0 24 24" fill="none" stroke="#fff" stroke-width="2"><path d="M5 3h4l2 5-2.5 1.5a11 11 0 0 0 6 6L16 13l5 2v4a2 2 0 0 1-2 2A16 16 0 0 1 3 5a2 2 0 0 1 2-2z"/></svg>
    (555) 214-0937
  </div>
</header>

<section class="hero">
  <svg class="abs" style="left:0;top:0" width="1200" height="640" role="img" aria-label="Jockey in red and white silks galloping a bay racehorse across a golden field at sunset">
    <defs>
      <linearGradient id="heroSky" x1="0" y1="0" x2="0" y2="1">
        <stop offset="0" stop-color="#7d7d86"/>
        <stop offset=".45" stop-color="#d39a5c"/>
        <stop offset=".75" stop-color="#c9a24a"/>
        <stop offset="1" stop-color="#b7913d"/>
      </linearGradient>
    </defs>
    <path fill="url(#heroSky)" d="M0 0H1200V560L1180 575 1160 560 1140 590 1110 578 1090 600 1060 588 1030 612 990 598 960 620 930 606 900 626 860 610 830 632 790 616 760 636 720 622 690 640 650 624 610 640 570 626 530 638 500 620 460 634 420 616 380 630 340 612 300 626 260 608 220 620 180 600 140 612 100 594 60 604 30 586 0 596Z"/>
  </svg>
  <div class="hero-badge">
    <div class="hero-badge-inner">
      <div class="lead">WE SUPPORT AND DEVELOP<br>RETIRED THOROUGHBRED</div>
      <div class="big">RACEHORSES<br>FOR THEIR NEXT<br>CHAPTER IN LIFE</div>
    </div>
  </div>
  <svg class="hero-arrow" style="left:46px" width="28" height="48" viewBox="0 0 28 48"><path d="M24 2 4 24l20 22" fill="none" stroke="#fff" stroke-width="4"/></svg>
  <svg class="hero-arrow" style="left:1138px" width="28" height="48" viewBox="0 0 28 48"><path d="M4 2l20 22L4 46" fill="none" stroke="#fff" stroke-width="4"/></svg>
</section>

<svg class="tl" viewBox="0 0 1200 4024">
  <g fill="none" stroke="var(--grey-line)" stroke-width="2">
    <path d="M606 719V842"/>
    <path d="M798 1219V1250Q798 1305 735 1305H390Q328 1305 328 1360V1410"/>
    <path d="M348 1766Q348 1851 420 1851H740Q820 1851 820 1920V1944"/>
    <path d="M595 2383V2458"/>
    <path d="M598 3109V3222"/>
  </g>
  <g fill="#fff" stroke="var(--red)" stroke-width="3">
    <circle cx="606" cy="850" r="7"/>
    <circle cx="328" cy="1419" r="7"/>
    <circle cx="820" cy="1952" r="7"/>
    <circle cx="595" cy="2466" r="7"/>
    <circle cx="598" cy="3230" r="7"/>
  </g>
</svg>

<!-- retire retrain rehome -->
<svg class="abs" style="left:0;top:778px" width="560" height="482" role="img" aria-label="Chestnut horse standing in a green pasture">
  <defs><linearGradient id="g1" x1="0" y1="0" x2="1" y2="1"><stop offset="0" stop-color="#4f7a35"/><stop offset=".5" stop-color="#9a5a2a"/><stop offset="1" stop-color="#5d8a3c"/></linearGradient></defs>
  <path fill="url(#g1)" d="M0 150 40 120 90 90 150 80 200 30 250 20 300 0 340 30 400 40 450 60 520 50 555 90 540 150 556 200 520 250 500 310 460 360 430 400 380 410 330 440 280 430 220 462 160 450 100 470 40 482 0 470Z"/>
</svg>
<h2 class="sect-title" style="left:600px;top:828px;width:504px;font-size:37px;line-height:43px">RETIRE. RETRAIN.<br>REHOME.</h2>
<p class="copy" style="left:600px;top:932px;width:504px;font-size:17px;line-height:30px;font-weight:600;color:#222">Fernvale Quillstone Heritage Society (FQHS) is a<br>registered not-for-profit organization in Fernvale.</p>
<p class="copy" style="left:600px;top:1010px;width:504px;font-size:14px;line-height:28px">Lorem Ipsum is simply dummy text of the printing and typesetting<br>industry. Lorem Ipsum has been the industry's standard dummy text<br>ever since the 1500s, when an unknown printer</p>
<div class="btn-outline" style="left:755px;top:1116px;width:189px;height:46px">LEARN MORE</div>

<!-- what is aftercare -->
<h2 class="sect-title" style="left:90px;top:1442px;width:486px;font-size:34px;line-height:40px">WHAT IS THOROUGHBRED<br>AFTERCARE?</h2>
<p class="copy" style="left:110px;top:1532px;width:446px;font-size:13.4px;line-height:21px;color:#333">The health, safety and welfare of our equine athletes does not end at the finish line, and retirement and aftercare are critical to the success of the racing industry. Aftercare is the safe placement of racehorses after their careers as racehorse are completed. Some horses might retire to the breeding shed or broodmare bands, while others are retrained for second careers.</p>
<div class="btn-outline" style="left:220px;top:1684px;width:227px;height:44px;font-size:12.5px">LEARN MORE ABOUT US</div>
<svg class="abs" style="left:575px;top:1344px" width="598" height="454" role="img" aria-label="Young woman resting her cheek against a dark bay horse outdoors">
  <defs><linearGradient id="g2" x1="0" y1="0" x2="1" y2="1"><stop offset="0" stop-color="#6d8a3a"/><stop offset=".45" stop-color="#2e2622"/><stop offset=".75" stop-color="#d9b891"/><stop offset="1" stop-color="#6b5a40"/></linearGradient></defs>
  <path fill="url(#g2)" d="M30 120 80 70 140 60 200 20 260 10 300 30 350 0 400 40 460 50 500 100 560 150 598 230 580 290 560 340 520 380 470 400 420 420 360 454 300 440 240 420 170 400 120 360 80 330 40 290 10 230 0 170Z"/>
</svg>

<!-- adopt -->
<svg class="abs" style="left:0;top:1903px" width="566" height="488" role="img" aria-label="Hand reaching up to stroke a chestnut horse's neck in warm light">
  <defs><linearGradient id="g3" x1="0" y1="0" x2="1" y2="1"><stop offset="0" stop-color="#5a2a12"/><stop offset=".5" stop-color="#b5601f"/><stop offset="1" stop-color="#d98a3a"/></linearGradient></defs>
  <path fill="url(#g3)" d="M0 80 60 60 120 70 170 40 240 20 290 0 350 30 410 20 470 60 540 70 566 130 548 190 560 260 520 310 500 370 440 410 380 420 320 450 250 430 180 460 110 450 60 488 0 470Z"/>
</svg>
<div class="adopt-ring">
  <div class="adopt-disc">
    <h2 class="serif" style="position:absolute;left:0;top:158px;width:100%;font-size:36px;color:#fff">ADOPT A HORSE</h2>
    <p style="position:absolute;left:0;top:214px;width:100%;font-size:16px;line-height:32px">Fernvale Quillstone Heritage is committed<br>to helping match you with the perfect horse.</p>
    <div style="position:absolute;left:124px;top:296px;width:184px;height:43px;border-radius:22px;background:#fff;color:var(--red);font-size:14px;font-weight:700;display:flex;align-items:center;justify-content:center">ADOPT NOW</div>
  </div>
</div>

<!-- horses -->
<h2 class="section-heading" style="top:2492px">OUR HORSES</h2>
<div class="horse-card" style="left:88px;top:2578px"><svg width="332" height="235" role="img" aria-label="Chestnut horse with flowing mane in a meadow"><defs><linearGradient id="h1" x1="0" y1="0" x2="1" y2="1"><stop offset="0" stop-color="#9bb25a"/><stop offset=".6" stop-color="#a65a24"/><stop offset="1" stop-color="#5e8a2f"/></linearGradient></defs><rect width="332" height="235" fill="url(#h1)"/></svg></div>
<div class="horse-card" style="left:438px;top:2578px">
  <svg width="332" height="235" role="img" aria-label="Bay horse portrait against a dark background"><defs><linearGradient id="h2" x1="0" y1="0" x2="1" y2="1"><stop offset="0" stop-color="#2a2523"/><stop offset=".6" stop-color="#5a3420"/><stop offset="1" stop-color="#222"/></linearGradient></defs><rect width="332" height="235" fill="url(#h2)"/></svg>
  <div class="horse-info">
    <div class="name">Silver Larkspur</div>
    <div class="facts"><div><b>Birth Year:</b> 2018</div><div><b>Color:</b> Bay</div><div><b>Gender:</b> Gelding</div><div><b>Location:</b> Marrowdale</div></div>
  </div>
</div>
<div class="horse-card" style="left:788px;top:2578px"><svg width="332" height="235" role="img" aria-label="Black horse standing in a field of red poppies"><defs><linearGradient id="h3" x1="0" y1="0" x2="0" y2="1"><stop offset="0" stop-color="#9fb0bd"/><stop offset=".45" stop-color="#5c7046"/><stop offset=".7" stop-color="#c8382a"/><stop offset="1" stop-color="#a8281e"/></linearGradient></defs><rect width="332" height="235" fill="url(#h3)"/></svg></div>
<div class="horse-card" style="left:88px;top:2831px"><svg width="332" height="235" role="img" aria-label="Brown horse wearing a halter in autumn woods"><defs><linearGradient id="h4" x1="0" y1="0" x2="1" y2="1"><stop offset="0" stop-color="#b88060"/><stop offset=".5" stop-color="#4a2a1a"/><stop offset="1" stop-color="#a0522d"/></linearGradient></defs><rect width="332" height="235" fill="url(#h4)"/></svg></div>
<div class="horse-card" style="left:438px;top:2831px"><svg width="332" height="235" role="img" aria-label="Bay horse trotting on green grass"><defs><linearGradient id="h5" x1="0" y1="0" x2="1" y2="1"><stop offset="0" stop-color="#b5bf6a"/><stop offset=".5" stop-color="#b8682c"/><stop offset="1" stop-color="#7fa043"/></linearGradient></defs><rect width="332" height="235" fill="url(#h5)"/></svg></div>
<div class="horse-card" style="left:788px;top:2831px"><svg width="332" height="235" role="img" aria-label="Grey horse at golden hour"><defs><linearGradient id="h6" x1="0" y1="0" x2="1" y2="1"><stop offset="0" stop-color="#c99a48"/><stop offset=".55" stop-color="#6e6256"/><stop offset="1" stop-color="#3d3a35"/></linearGradient></defs><rect width="332" height="235" fill="url(#h6)"/></svg></div>

<div class="btn-solid" style="left:469px;top:3109px;width:264px;height:57px;z-index:0">MORE WAYS TO GIVE</div>

<h2 class="section-heading" style="top:3254px">CONTACT US</h2>

<!-- contact -->
<div class="footer-band" role="img" aria-label="Dimmed photo of horses grazing at dusk"></div>
<div class="contact-card">
  <svg class="abs" style="left:0;top:0" width="974" height="398"><path d="M0 0H391V300Q391 380 460 398H0Z" fill="var(--red)"/></svg>
  <div class="contact-item" style="top:72px">
    <div class="icon" style="top:0"><svg width="26" height="26" viewBox="0 0 24 24" fill="none" stroke="var(--red)" stroke-width="1.6"><path d="M12 22s7-7 7-12a7 7 0 0 0-14 0c0 5 7 12 7 12z"/><circle cx="12" cy="10" r="2.5"/></svg></div>
    <div class="label" style="left:78px;top:0">LOCATION</div>
    <div class="val" style="left:78px;top:14px">Brindlecove, Fernvale Valley<br>4210 Range Road 88, PO Box 602</div>
  </div>
  <div class="contact-item" style="top:164px">
    <div class="icon" style="top:0"><svg width="26" height="26" viewBox="0 0 24 24" fill="none" stroke="var(--red)" stroke-width="1.6"><path d="M5 3h4l2 5-2.5 1.5a11 11 0 0 0 6 6L16 13l5 2v4a2 2 0 0 1-2 2A16 16 0 0 1 3 5a2 2 0 0 1 2-2z"/></svg></div>
    <div class="label" style="left:78px;top:6px">PHONE NUMBER</div>
    <div class="val" style="left:78px;top:20px;font-size:13px">(555) 214-0937</div>
  </div>
  <div class="contact-item" style="top:256px">
    <div class="icon" style="top:0"><svg width="28" height="22" viewBox="0 0 28 22" fill="none" stroke="var(--red)" stroke-width="1.6"><rect x="2" y="2" width="24" height="18"/><path d="M2 2l12 10L26 2"/></svg></div>
    <div class="label" style="left:78px;top:6px">EMAIL US</div>
    <div class="val" style="left:78px;top:20px;font-size:12px">hello@fernvalequillstone.org</div>
  </div>

  <div class="field" style="left:455px;top:72px;width:206px">&#9679; First Name</div>
  <div class="field" style="left:685px;top:72px;width:208px">&#9679; Last Name</div>
  <div class="field" style="left:455px;top:144px;width:206px">&#9993; E-mail address</div>
  <div class="field" style="left:685px;top:144px;width:208px">&#9742; Phone</div>
  <div class="field" style="left:455px;top:204px;width:438px;height:79px;align-items:flex-start">&#9679; Message</div>
  <div class="check-box"><span class="box"></span>I'm not a robot</div>
  <div class="send-btn">SEND MESSAGE</div>
</div>

<!-- footer -->
<div class="footer-brand">Fernvale Quillstone Heritage Society</div>
<nav class="footer-nav">
  <a style="left:334px">HOME</a>
  <a style="left:436px">ABOUT</a>
  <a style="left:542px">ADOPT</a>
  <a style="left:653px">HORSES</a>
  <a style="left:767px">DONATE</a>
  <a style="left:891px">CONTACT</a>
</nav>
<p class="copyright">©2021 Copyright Fernvale. All Right Reserved</p>

</body>
</html>
```